Stylish business cards for KV7

To create an appealing and professional business card design for a WOMEN Owned Construction Supply Company.
2 sided card. Incorporate brand elements, curvy, colorful, sleek and bright. No solid white background. attached samples of styles added shapes/ribbons. Want something with that WOW that looks awesome, factor. It is a new logo, so feel free to mess with logo colors in the blue and teal factors that can look good with both dark and light background. If you want to try a watermark with just the KV7, without the "Supply" that might look cool to.

Industry/Entity Type

Women owned construction supply company

Contact Information for Business Card

Name, Title, and phone number and email, web page. maybe spot for qr code.

Font styles to use
Sans Serif

Requirements
Nice to have
• would love to see colors, maybe stylish ribbon dividers or some sort of 2 or 3 tone color card that compliments logo.
Should not have
• Please do not have all white background. Do not include Home/reale state/ or building images.

```html
<!DOCTYPE html>
<html lang="en">
<head>
<meta charset="UTF-8">
<title>KV7 Supply — Business Cards</title>
<link rel="stylesheet" href="https://fonts.googleapis.com/css2?family=Montserrat:wght@400;700&display=swap">
<style>
  :root {
    --page-bg: #1b1b1c;
    --card-light-top: #f3f6f9;
    --card-light-bottom: #e2eaf2;
    --card-dark: #1c3a5b;
    --navy: #1b3a5c;
    --teal: #2596be;
    --teal-soft: rgba(37, 150, 190, 0.14);
    --ink: #3a3f45;
    --white: #ffffff;
    --watermark: rgba(255, 255, 255, 0.05);
  }
  * { box-sizing: border-box; margin: 0; padding: 0; }
  html, body {
    width: 1200px;
    height: 1059px;
    overflow: hidden;
    background: var(--page-bg);
    font-family: "Montserrat", sans-serif;
  }
  .canvas { position: relative; width: 1200px; height: 1059px; }

  .card {
    position: absolute;
    left: 256px;
    width: 690px;
    height: 392px;
    border-radius: 24px;
    overflow: hidden;
    box-shadow: 0 14px 30px rgba(0, 0, 0, 0.55);
  }
  .card--front {
    top: 89px;
    background: linear-gradient(160deg, var(--card-light-top) 0%, var(--card-light-bottom) 100%);
  }
  .card--back  { top: 547px; background: var(--card-dark); }

  .ribbons {
    position: absolute;
    inset: 0;
    width: 690px;
    height: 392px;
  }
  .ribbon--navy { fill: var(--navy); }
  .ribbon--teal { fill: var(--teal); }
  .ribbon--soft { fill: var(--teal-soft); }
  .ribbon--faint { fill: rgba(37, 150, 190, 0.18); }

  .brand-name {
    position: absolute;
    font-weight: 700;
    white-space: nowrap;
    letter-spacing: 0.5px;
  }
  .card--front .brand-name {
    left: 78px;
    top: 170px;
    font-size: 42px;
    color: var(--navy);
  }

  .divider {
    position: absolute;
    left: 343px;
    top: 99px;
    width: 1.5px;
    height: 197px;
    background: var(--teal);
  }

  .details { position: absolute; left: 380px; top: 96px; color: var(--ink); }
  .details__name {
    font-size: 25px;
    font-weight: 700;
    color: var(--navy);
    line-height: 1.1;
    letter-spacing: 0.3px;
  }
  .details__title { font-size: 16px; line-height: 1.3; }
  .details__address { margin-top: 22px; font-size: 16px; line-height: 22px; }
  .contact-list { list-style: none; margin-top: 14px; }
  .contact-list li {
    display: flex;
    align-items: center;
    gap: 8px;
    font-size: 16.5px;
    height: 27.5px;
    margin-left: -1px;
  }
  .contact-list svg { width: 13px; height: 13px; fill: none; stroke: var(--teal); flex: none; }
  .contact-list .icon-fill { fill: var(--teal); stroke: none; }

  .watermark {
    position: absolute;
    left: -10px;
    top: 60px;
    font-size: 250px;
    font-weight: 700;
    color: var(--watermark);
    line-height: 1;
    white-space: nowrap;
  }
  .card--back .brand-name {
    left: 210px;
    top: 166px;
    font-size: 52px;
    color: var(--white);
  }
</style>
</head>
<body>
<main class="canvas">

  <section class="card card--front" aria-label="Business card front">
    <svg class="ribbons" viewBox="0 0 690 392" aria-hidden="true">
      <path class="ribbon--soft" d="M470,0 C560,40 630,60 690,48 L690,0 Z"/>
      <path class="ribbon--soft" d="M560,0 C610,22 655,30 690,24 L690,0 Z"/>
      <path class="ribbon--teal" d="M0,336 C190,304 430,372 690,322 L690,336 C430,386 190,318 0,352 Z"/>
      <path class="ribbon--navy" d="M0,352 C190,318 430,386 690,336 L690,392 L0,392 Z"/>
    </svg>
    <div class="brand-name">KV7 Supply</div>
    <div class="divider"></div>
    <div class="details">
      <p class="details__name">DANA WHITFIELD</p>
      <p class="details__title">CEO/Founder</p>
      <p class="details__address">P.O Box 4127 Harbour Road<br>Westvale QC 40210</p>
      <ul class="contact-list">
        <li>
          <svg viewBox="0 0 24 24" aria-hidden="true"><path class="icon-fill" d="M6.6 10.8a15.1 15.1 0 0 0 6.6 6.6l2.2-2.2a1 1 0 0 1 1-.25 11.4 11.4 0 0 0 3.6.57 1 1 0 0 1 1 1V20a1 1 0 0 1-1 1A17 17 0 0 1 3 4a1 1 0 0 1 1-1h3.5a1 1 0 0 1 1 1c0 1.25.2 2.45.57 3.57a1 1 0 0 1-.25 1z"/></svg>
          555.014.0287
        </li>
        <li>
          <svg viewBox="0 0 24 24" aria-hidden="true"><path class="icon-fill" d="M2 5h20v14H2z"/><path d="M2 5l10 8 10-8M2 19l7-7M22 19l-7-7" stroke="#eaf0f5" stroke-width="1.8"/></svg>
          info@kv7supply.com.au
        </li>
        <li>
          <svg viewBox="0 0 24 24" aria-hidden="true" stroke-width="2"><circle cx="12" cy="12" r="10"/><path d="M2 12h20M12 2c3 3 3 17 0 20M12 2c-3 3-3 17 0 20"/></svg>
          www.kv7supply.com.au
        </li>
      </ul>
    </div>
  </section>

  <section class="card card--back" aria-label="Business card back">
    <div class="watermark" aria-hidden="true">KV7</div>
    <svg class="ribbons" viewBox="0 0 690 392" aria-hidden="true">
      <path class="ribbon--faint" d="M250,338 C420,318 560,326 690,340 L690,352 C560,338 420,330 250,346 Z"/>
    </svg>
    <div class="brand-name">KV7 Supply</div>
  </section>

</main>
</body>
</html>
```